Stylish new business card needed!

Hello everyone! I am in need of a new business card design for an alarm company here in Hurricane WV. I have all fonts, color codes and logos provided for you use! We are a young company and like the style of a clean sleek looking business card. Would like it double sided, one side holding the logo and the other with your design!
Target Market(s)
The people that are looking for the newest tech for home automation and security
Industry/Entity Type
Alarm services; Home automation
Contact Information for Business Card
Name of person; position (Sales; Installer); Phone Number (555.418.7260); Employee cell Number; Website (www.GuardedByVelk.example); Employee Email; Double sided
Look and feel
Each slider illustrates characteristics of the customer's brand and the style your logo design should communicate.

```html
<!DOCTYPE html>
<html lang="en">
<head>
<meta charset="utf-8">
<title>Velk Business Card</title>
<link rel="stylesheet" href="https://fonts.googleapis.com/css2?family=Montserrat:wght@400;500;700&display=swap">
<style>
  :root {
    --backdrop: #cfd3d3;
    --card-white: #f7f7f6;
    --brand-orange: #ee8441;
    --accent-orange: #d9661f;
    --ink-grey: #555657;
    --text-dark: #3c3d3e;
    --rule-grey: #9a9b9c;
    --logo-light: #eeeeee;
  }
  * { margin: 0; padding: 0; box-sizing: border-box; }
  html, body { width: 1200px; height: 829px; overflow: hidden; }
  body {
    background: var(--backdrop);
    font-family: "Montserrat", sans-serif;
    display: flex;
    align-items: center;
    justify-content: center;
    gap: 40px;
  }
  .card {
    width: 540px;
    height: 309px;
    position: relative;
    box-shadow: 0 10px 28px rgba(0,0,0,0.18);
  }
  .card-front { background: var(--card-white); }
  .card-back {
    background: var(--brand-orange);
    display: flex;
    align-items: center;
    justify-content: center;
  }
  .wordmark {
    font-weight: 500;
    letter-spacing: 0.04em;
    line-height: 1;
  }
  .card-front .wordmark {
    position: absolute;
    top: 44px;
    left: 0; right: 0;
    text-align: center;
    font-size: 76px;
    color: var(--ink-grey);
  }
  .card-back .wordmark {
    font-size: 110px;
    color: var(--logo-light);
  }
  .details {
    position: absolute;
    top: 158px;
    left: 0; right: 0;
    display: flex;
    justify-content: center;
  }
  .person {
    text-align: right;
    padding-right: 18px;
    border-right: 1px solid var(--rule-grey);
    padding-top: 4px;
  }
  .person-name {
    font-weight: 700;
    font-size: 17px;
    letter-spacing: 0.06em;
    color: var(--accent-orange);
    text-transform: uppercase;
  }
  .person-role {
    font-size: 12px;
    color: var(--text-dark);
    margin-top: 2px;
  }
  .contact-list {
    list-style: none;
    padding-left: 16px;
    font-size: 12.5px;
    color: var(--text-dark);
  }
  .contact-list li {
    display: flex;
    align-items: center;
    gap: 7px;
    height: 21px;
  }
  .contact-list svg { width: 12px; height: 12px; flex: none; }
  .address {
    position: absolute;
    top: 250px;
    left: 0; right: 0;
    text-align: center;
    font-size: 12.5px;
    color: var(--text-dark);
  }
</style>
</head>
<body>
  <section class="card card-front">
    <div class="wordmark">VELK</div>
    <div class="details">
      <div class="person">
        <div class="person-name">Dana Whitlock</div>
        <div class="person-role">Sales/Installer</div>
      </div>
      <ul class="contact-list">
        <li>
          <svg viewBox="0 0 12 12" aria-hidden="true"><path fill="#d9661f" d="M2.6 1l1.8 2.2-1 1.2c.7 1.5 1.7 2.5 3.2 3.2l1.2-1L10 8.4 9 10.6C5 10.4 1.6 7 1.4 3z"/></svg>
          <span>555.418.7260</span>
        </li>
        <li>
          <svg viewBox="0 0 12 12" aria-hidden="true"><rect x="1" y="2.5" width="10" height="7" fill="#d9661f"/><path d="M1 2.5l5 4 5-4" fill="none" stroke="#fff" stroke-width="1"/></svg>
          <span>info@GuardedByVelk.example</span>
        </li>
        <li>
          <svg viewBox="0 0 12 12" aria-hidden="true"><circle cx="6" cy="6" r="5" fill="#d9661f"/><path d="M1 6h10M6 1c-2.5 3-2.5 7 0 10M6 1c2.5 3 2.5 7 0 10" fill="none" stroke="#fff" stroke-width=".7"/></svg>
          <span>www.GuardedByVelk.example</span>
        </li>
      </ul>
    </div>
    <p class="address">1480 W Harlow Avenue Brenton County Name 4417</p>
  </section>

  <section class="card card-back">
    <div class="wordmark">VELK</div>
  </section>
</body>
</html>
```